Birch And Harbor Website A Website design for book editing

A website design for book editing

Our proofreading, editing and manuscript review packages are specifically tailored to help you publish the best possible version of your story.

NEED HELP PUBLISHING A BESTSELLER?

If you’re looking for professional book editing services from senior publishing industry insiders, look no further. Besides editing, we can also answer all your publishing questions and get you started building your author platform.

OUR SERVICES

We've carefully structured our packages to maximize value for every budget.

PRICING

$.02
PER WORD
Proofreading
Line Edit (Copy-editing)
Fix spelling and grammar
Sales copy/summary revision

$.04
PER WORD
Proofreading
Line Edit (Copy-editing)
Fix spelling and grammar
Organization and content
Plot and pacing
Manuscript Review

$.06
PER WORD
Proofreading
Line Edit (Copy-editing)
Fix spelling and grammar
Organization and content
Plot and pacing
Manuscript Review
Formatting (print and ebook)
Pre-publication proofread

OUR PROCESS

Send us a sample of your book. Our caffeine-fueled, eagle-eyed editors will go through it and then email you with their comments and suggestions. You can ask them any questions you want. They will look for…

Typos and grammatical errors.
Spelling and word choice issues
Punctuation and style
Word choice, clarity and flow.
Sentence structure and craft
If your writing is already clean, then they’ll discuss bigger picture things with you, like theme, concept, purpose, audience, potential market and branding (including title, subtitle, and tagline or elevator pitch).

Once you feel comfortable and confident in an editor’s expertise, skill and knowledge, and are ready to move ahead, we’ll send an invoice for the first half of the total word count so the editor can get started. We’ll charge the rest when the project is close to completion.

Target Market(s)

Authors

Industry/Entity Type

Book Publisher

Coding

Coded - Design and coding required

Number of Pages Required

1 page

Requirements
Must have
• OUR SERVICES
• We've carefully structured our packages to maximize value for every budget.
• PRICING
• $.02
• PER WORD
• Proofreading
• Line Edit (Copy-editing)
• Fix spelling and grammar
• Sales copy/summary revision
• $.04
• PER WORD
• Proofreading
• Organization and content
• Plot and pacing
• Manuscript Review
• $.06
• PER WORD
• Proofreading
• Plot and pacing
• Manuscript Review
• Formatting (print and ebook)
• Pre-publication proofread

```html
<!DOCTYPE html>
<html lang="en">
<head>
<meta charset="utf-8">
<title>Birch And Harbor — Book Editing</title>
<link rel="stylesheet" href="https://fonts.googleapis.com/css2?family=Montserrat:wght@600;700&family=Open+Sans:wght@400;600;700;800&family=Questrial&display=swap">
<style>
:root{
  --red:#d8101f;
  --red-dark:#a50d18;
  --ink:#1f1f1f;
  --text:#555;
  --muted:#777;
  --pink:#fdeef0;
  --card-dark:#333233;
  --footer:#1b1b1b;
  --white:#fff;
}
*{margin:0;padding:0;box-sizing:border-box}
html,body{width:1200px;height:3805px;overflow:hidden}
body{position:relative;background:var(--white);font-family:"Open Sans",Arial,sans-serif;color:var(--text)}
.abs{position:absolute}

/* header */
.site-header{position:absolute;left:0;top:0;width:1200px;height:90px;background:var(--white)}
.brand{position:absolute;left:100px;top:26px;display:flex;align-items:center;gap:10px;font-family:"Montserrat",sans-serif;font-weight:700;font-size:28px;color:var(--red)}
.brand-dot{width:16px;height:16px;border-radius:50%;background:var(--red)}
.main-nav a{position:absolute;top:37px;font-family:"Questrial",sans-serif;font-size:15px;color:var(--ink);text-decoration:none}

/* hero */
.hero{position:absolute;left:0;top:90px;width:1200px;height:582px;overflow:hidden}
.hero-photo{position:absolute;inset:0;background:linear-gradient(120deg,#4a3c34 0%,#7a6a5e 35%,#b8aea4 55%,#6a5a50 75%,#3a2e28 100%)}
.hero-shade{position:absolute;inset:0;background:rgba(20,14,12,.45)}
.hero-title{position:absolute;left:0;top:150px;width:1200px;text-align:center;font-weight:700;font-size:56px;line-height:71px;color:var(--white);letter-spacing:1px}
.btn{display:inline-flex;align-items:center;justify-content:center;background:var(--red);color:var(--white);font-family:"Open Sans",sans-serif;text-decoration:none}
.hero-btn{position:absolute;left:512px;top:312px;width:174px;height:48px;font-size:17px;gap:10px}
.hero-wave{position:absolute;left:0;top:0}

/* about / why */
.section-title{font-family:"Questrial",sans-serif;color:var(--ink);font-weight:400}
.about-title{position:absolute;left:100px;top:742px;font-size:40px}
.about-photo{position:absolute;left:100px;top:832px;width:337px;height:267px;background:linear-gradient(135deg,#dfe6ec 0%,#b8c4cc 40%,#6b6660 70%,#3b3533 100%)}
.about-lead{position:absolute;left:477px;top:824px;width:260px;font-size:14px;line-height:35px;color:var(--red);text-transform:uppercase}
.about-body{position:absolute;left:477px;top:943px;width:240px;font-size:14px;line-height:33px;color:var(--muted)}
.why-title{position:absolute;left:789px;top:780px;font-size:40px}
.why-body{position:absolute;left:789px;top:858px;width:310px;font-size:14px;line-height:35px;color:var(--muted)}
.why-btn{position:absolute;left:789px;top:1060px;width:122px;height:44px;font-size:14px}

/* services */
.service-head{position:absolute;left:100px;top:1236px;display:flex;align-items:baseline;gap:14px}
.service-head h2{font-size:40px}
.service-head p{font-size:13px;color:var(--ink);text-transform:uppercase}
.service-rule{position:absolute;left:100px;top:1299px;width:1000px;height:1px;background:#ddd}
.pink-wave{position:absolute;left:0;top:1500px}

.price-card{position:absolute;background:var(--white);box-shadow:0 6px 24px rgba(0,0,0,.08);text-align:center}
.price-card .tag{position:absolute;left:28px;width:236px;height:104px;display:flex;flex-direction:column;align-items:center;justify-content:center}
.tag-name{font-size:17px}
.tag-price{font-weight:700;font-size:30px;line-height:36px}
.tag-price small{font-weight:400;font-size:13px}
.price-card .bar{position:absolute;left:117px;width:58px;height:2px;background:var(--red)}
.price-card ul{position:absolute;left:0;width:100%;list-style:none;font-size:15px;line-height:34px;color:var(--muted)}
.card-basic,.card-premium{top:1428px;width:292px;height:399px}
.card-basic{left:101px}.card-premium{left:802px}
.card-basic .tag,.card-premium .tag{top:26px;background:var(--card-dark);color:var(--white)}
.card-basic .bar,.card-premium .bar{top:175px}
.card-basic ul,.card-premium ul{top:200px}
.card-standard{left:451px;top:1393px;width:297px;height:479px;background:linear-gradient(160deg,var(--red) 0%,#8a1019 45%,#2a2525 100%)}
.card-standard .tag{top:24px;left:30px;background:var(--white);color:var(--red)}
.card-standard .bar{top:168px;left:120px;background:var(--white)}
.card-standard ul{top:184px;color:var(--white)}
.start-btn{position:absolute;left:512px;top:1923px;width:173px;height:46px;font-size:17px}

/* process */
.process-title{position:absolute;left:0;top:2266px;width:1200px;text-align:center;font-size:40px}
.process-intro{position:absolute;left:170px;top:2360px;width:860px;text-align:center;font-size:14px;line-height:36px;color:var(--muted)}
.step{position:absolute;width:300px;text-align:center}
.step-icon{display:block;margin:0 auto}
.step h3{margin-top:22px;font-family:"Open Sans",sans-serif;font-weight:600;font-size:18px;line-height:30px;color:var(--ink)}
.step p{margin-top:14px;font-size:14px;line-height:29px;color:var(--muted)}

/* newsletter */
.news-band{position:absolute;left:0;top:3278px;width:1200px;height:167px;background:var(--red)}
.news-input{position:absolute;left:142px;top:61px;width:330px;height:46px;background:var(--white);font-size:14px;color:#555;padding:14px 16px}
.news-btn{position:absolute;left:472px;top:61px;width:129px;height:46px;background:var(--footer);font-size:14px;letter-spacing:1px}
.socials{position:absolute;left:880px;top:68px;display:flex;gap:10px}
.socials span{width:38px;height:38px;border-radius:50%;background:var(--footer)}

/* footer */
.site-footer{position:absolute;left:0;top:3445px;width:1200px;height:360px;background:var(--footer);color:#ddd}
.foot-col{position:absolute;top:72px}
.foot-col h4{font-family:"Questrial",sans-serif;font-weight:400;font-size:16px;color:var(--white);margin-bottom:14px}
.foot-col li{list-style:none;font-size:13px;line-height:26px;color:#ccc;padding-left:16px;position:relative}
.foot-col li::before{content:"";position:absolute;left:0;top:10px;border-left:6px solid #ccc;border-top:4px solid transparent;border-bottom:4px solid transparent}
.foot-rule{position:absolute;left:100px;top:305px;width:1000px;height:1px;background:#333}
.copyright{position:absolute;left:0;top:322px;width:1200px;text-align:center;font-size:13px;color:#ccc}
</style>
</head>
<body>

<header class="site-header">
  <div class="brand"><span class="brand-dot"></span>Birch And Harbor</div>
  <nav class="main-nav">
    <a style="left:520px">Home</a>
    <a style="left:595px">About Us</a>
    <a style="left:690px">Services</a>
    <a style="left:780px">Pricing</a>
    <a style="left:860px">Customer</a>
    <a style="left:960px">Blog</a>
    <a style="left:1025px">Contact Us</a>
  </nav>
</header>

<section class="hero">
  <div class="hero-photo" role="img" aria-label="Hands turning through a stack of printed manuscript pages on a desk"></div>
  <div class="hero-shade"></div>
  <h1 class="hero-title">NEED HELP PUBLISHING<br>A BESTSELLER?</h1>
  <a class="btn hero-btn">Learn More
    <svg width="18" height="12" viewBox="0 0 18 12"><path d="M0 6h14M10 1l5 5-5 5" stroke="#fff" stroke-width="2.4" fill="none"/></svg>
  </a>
  <svg class="hero-wave" width="1200" height="582" viewBox="0 0 1200 582">
    <path d="M0 500 C250 610 600 600 1200 470 L1200 582 L0 582 Z" fill="#fff"/>
    <path d="M0 485 C250 595 600 585 1200 455" stroke="#d8101f" stroke-width="5" fill="none"/>
    <circle cx="1070" cy="521" r="27" fill="none" stroke="#fff" stroke-width="2"/>
    <path d="M1062 512l8 8 8-8M1062 521l8 8 8-8" stroke="#fff" stroke-width="2.2" fill="none"/>
  </svg>
</section>

<h2 class="section-title about-title">About Us</h2>
<div class="about-photo" role="img" aria-label="Person working on a laptop beside a bright office window"></div>
<p class="about-lead">We provide professional<br>book editing services from<br>senior publishing industry</p>
<p class="about-body">Our proofreading, editing and manuscript review packages are specifically tailored to help you publish the best possible version of your story.</p>

<h2 class="section-title why-title">Why Choose Us</h2>
<p class="why-body">If your writing is already clean, then they'll discuss bigger picture things with you, like theme,concept, purpose, audience, potential market and branding (including title, subtitle, and tagline or elevator pitch).</p>
<a class="btn why-btn">Read More</a>

<div class="service-head"><h2 class="section-title">Our Service</h2><p>( We've carefully structured our packages to maximize value for every budget. )</p></div>
<div class="service-rule"></div>

<svg class="pink-wave" width="1200" height="760" viewBox="0 0 1200 760">
  <path d="M0 170 C300 80 700 230 1200 20 L1200 600 C900 500 600 620 300 690 C180 720 80 730 0 720 Z" fill="#fdeef0"/>
</svg>

<div class="price-card card-basic">
  <div class="tag"><span class="tag-name">Basic</span><span class="tag-price">$.02 <small>Per Word</small></span></div>
  <div class="bar"></div>
  <ul><li>Proofreading</li><li>Line Edit (Copy-editing)</li><li>Fix spelling and grammar</li><li>Sales copy/summary revision</li></ul>
</div>

<div class="price-card card-standard">
  <div class="tag"><span class="tag-name">Standard</span><span class="tag-price">$.04 <small>Per Word</small></span></div>
  <div class="bar"></div>
  <ul><li>Proofreading</li><li>Line Edit (Copy-editing)</li><li>Fix spelling and grammar</li><li>Sales copy/summary revision</li><li>Organization and content</li><li>Plot and pacing</li><li>Manuscript Review</li></ul>
</div>

<div class="price-card card-premium">
  <div class="tag"><span class="tag-name">Premium</span><span class="tag-price">$.06 <small>Per Word</small></span></div>
  <div class="bar"></div>
  <ul><li>Proofreading</li><li>Line Edit (Copy-editing)</li><li>Fix spelling and grammar</li><li>Sales copy/summary revision</li><li>Organization and content...</li></ul>
</div>

<a class="btn start-btn">Get Started</a>

<h2 class="section-title process-title">Our Process</h2>
<p class="process-intro">Send us a sample of your book. Our caffeine-fueled, eagle-eyed editors will go through it and then email you with their comments and suggestions. You can ask them any questions you want. They will look for...</p>

<div class="step" style="left:106px;top:2482px">
  <svg class="step-icon" width="100" height="100" viewBox="0 0 100 100"><circle cx="50" cy="50" r="49" fill="#fff" stroke="#ddd"/><path d="M36 58l8-22 8 22M39 50h10M50 60l6 6 12-14" stroke="#d8101f" stroke-width="3" fill="none" stroke-linecap="round"/></svg>
  <h3>Typos and<br>grammatical errors.</h3>
  <p>Sed ut perspiciatis unde<br>omnis iste natus error sit voluptatem<br>accusantium doloremque laudan...</p>
</div>
<div class="step" style="left:449px;top:2482px">
  <svg class="step-icon" width="100" height="100" viewBox="0 0 100 100"><circle cx="50" cy="50" r="49" fill="#d8101f"/><rect x="37" y="34" width="24" height="32" rx="2" fill="none" stroke="#fff" stroke-width="3"/><path d="M42 42h14M42 49h14M42 56h9M58 62l8-16" stroke="#fff" stroke-width="3" stroke-linecap="round"/></svg>
  <h3>Spelling and word<br>choice issues</h3>
  <p>Sed ut perspiciatis unde<br>omnis iste natus error sit voluptatem<br>accusantium doloremque laudan...</p>
</div>
<div class="step" style="left:794px;top:2482px">
  <svg class="step-icon" width="100" height="100" viewBox="0 0 100 100"><circle cx="50" cy="50" r="49" fill="#fff" stroke="#ddd"/><path d="M36 38h28v20H48l-8 7v-7h-4z" fill="none" stroke="#d8101f" stroke-width="3" stroke-linejoin="round"/><path d="M45 45v5M54 45v5" stroke="#d8101f" stroke-width="3" stroke-linecap="round"/></svg>
  <h3>Punctuation<br>and style</h3>
  <p>Sed ut perspiciatis unde<br>omnis iste natus error sit voluptatem<br>accusantium doloremque laudan...</p>
</div>
<div class="step" style="left:276px;top:2855px">
  <svg class="step-icon" width="100" height="100" viewBox="0 0 100 100"><circle cx="50" cy="50" r="49" fill="#fff" stroke="#ddd"/><circle cx="47" cy="47" r="11" fill="none" stroke="#d8101f" stroke-width="3"/><path d="M55 55l10 10" stroke="#d8101f" stroke-width="4" stroke-linecap="round"/></svg>
  <h3>Word choice,<br>clarity and flow.</h3>
  <p>Sed ut perspiciatis unde<br>omnis iste natus error sit voluptatem<br>accusantium doloremque laudan...</p>
</div>
<div class="step" style="left:621px;top:2855px">
  <svg class="step-icon" width="100" height="100" viewBox="0 0 100 100"><circle cx="50" cy="50" r="49" fill="#fff" stroke="#ddd"/><path d="M38 33h18l6 6v28H38z" fill="none" stroke="#d8101f" stroke-width="3" stroke-linejoin="round"/><path d="M43 44h12M43 51h12M43 58h7" stroke="#d8101f" stroke-width="3" stroke-linecap="round"/><circle cx="60" cy="60" r="5" fill="#fff" stroke="#d8101f" stroke-width="3"/></svg>
  <h3>Sentence structure<br>and craft</h3>
  <p>Sed ut perspiciatis unde<br>omnis iste natus error sit voluptatem<br>accusantium doloremque laudan...</p>
</div>

<section class="news-band">
  <div class="news-input">Enter Your Email Addresss</div>
  <a class="btn news-btn">SUBSCRIBE</a>
  <div class="socials"><span></span><span></span><span></span><span></span></div>
</section>

<footer class="site-footer">
  <div class="foot-col" style="left:145px"><h4>NAVIGATE</h4><ul><li>Home</li><li>About Us</li><li>Services</li><li>Customer</li><li>Blog</li><li>Contact Us</li></ul></div>
  <div class="foot-col" style="left:411px"><h4>OTHER LINKS</h4><ul><li>Faq</li><li>Privacy Policy</li><li>Terms Of Service</li><li>Sitemap</li></ul></div>
  <div class="foot-col" style="left:693px"><h4>IMPORTANT</h4><ul><li>Process</li><li>Editing</li><li>Help</li></ul></div>
  <div class="foot-col" style="left:989px"><h4>ACCOUNT</h4><ul><li>Sign In</li><li>My Account</li></ul></div>
  <div class="foot-rule"></div>
  <p class="copyright">© Copyrights 2018 Birch And Harbor All Rights Reserved</p>
</footer>

</body>
</html>
```